Duct Manufacturing Company new to the industry needs business card and stationary design

we are sheet metal duct manufacturers looking for a business card design to fit my new business logo.
nothing to crazy that will date, but want it to stand out from the crowed.
I'm sure you guys will work it out.

Contact Information for Business Card

Glen Marsh
Director

Address
17 Dorwell St
Tallowmere NSW 2794

0438 760 514

Sales@flowbend.com.au

Font styles to use
Other font styles liked:
• BankGothic md bt

Requirements
Nice to have
• Like the idea of corner rounded to match logo
• like to keep colours flowing
• font I like sharp square not rounded

```html
<!DOCTYPE html>
<html lang="en">
<head>
<meta charset="utf-8">
<title>Flowbend Industries – Business Card</title>
<link rel="stylesheet" href="https://fonts.googleapis.com/css2?family=Michroma&display=swap">
<style>
  :root {
    --page-bg: #e9eaec;
    --card-white: #f7f8f8;
    --blue-deep: #0b5cad;
    --blue-mid: #1477c9;
    --blue-light: #1fa6dc;
    --green: #7cc242;
    --grey: #8d9196;
    --ink: #111111;
    --text-white: #ffffff;
  }
  * { margin: 0; padding: 0; box-sizing: border-box; }
  html, body {
    width: 1200px;
    height: 780px;
    overflow: hidden;
    background: var(--page-bg);
    font-family: "Michroma", "Arial", sans-serif;
  }
  .canvas {
    position: relative;
    width: 1200px;
    height: 780px;
  }
  .business-card {
    position: absolute;
    left: 150px;
    top: 115px;
    width: 900px;
    height: 550px;
    border-radius: 26px;
    overflow: hidden;
    background: var(--card-white);
    box-shadow: 0 14px 40px rgba(0, 0, 0, 0.18);
  }
  .card-backdrop {
    position: absolute;
    inset: 0;
  }
  .brand {
    position: absolute;
    left: 62px;
    top: 78px;
    display: flex;
    align-items: center;
    gap: 22px;
  }
  .brand-dot {
    width: 66px;
    height: 66px;
    border-radius: 50%;
    background: var(--blue-mid);
    flex-shrink: 0;
  }
  .brand-name {
    color: var(--green);
    font-size: 40px;
    line-height: 1.15;
    letter-spacing: 1px;
    text-transform: uppercase;
  }
  .contact-person {
    position: absolute;
    left: 62px;
    top: 232px;
    font-size: 22px;
    letter-spacing: 2px;
    text-transform: uppercase;
    color: var(--green);
  }
  .contact-person .divider { color: var(--ink); margin: 0 10px; }
  .contact-person .role { color: var(--blue-light); font-size: 18px; }
  .contact-list {
    position: absolute;
    left: 62px;
    top: 290px;
    list-style: none;
  }
  .contact-item {
    display: flex;
    align-items: center;
    gap: 14px;
    font-size: 19px;
    letter-spacing: 2px;
    color: var(--ink);
    text-transform: uppercase;
    margin-bottom: 16px;
  }
  .contact-icon {
    width: 22px;
    height: 22px;
    flex-shrink: 0;
  }
  .address {
    position: absolute;
    right: 44px;
    bottom: 56px;
    text-align: right;
    color: var(--text-white);
    font-style: normal;
    font-size: 17px;
    line-height: 1.9;
    letter-spacing: 2px;
    text-transform: uppercase;
  }
</style>
</head>
<body>
<main class="canvas">
  <section class="business-card">
    <svg class="card-backdrop" width="900" height="550" viewBox="0 0 900 550" aria-hidden="true">
      <defs>
        <linearGradient id="band-gradient" x1="0" y1="1" x2="1" y2="0">
          <stop offset="0" stop-color="#0a55a6"/>
          <stop offset="0.55" stop-color="#1479cb"/>
          <stop offset="1" stop-color="#20b0e0"/>
        </linearGradient>
      </defs>
      <rect class="blue-band" width="900" height="550" fill="url(#band-gradient)"/>
      <ellipse class="white-arch" cx="250" cy="190" rx="450" ry="320" fill="#f7f8f8" stroke="#111111" stroke-width="5"/>
    </svg>

    <div class="brand">
      <span class="brand-dot"></span>
      <div class="brand-name">Flowbend<br>Industries</div>
    </div>

    <p class="contact-person">Glen Marsh<span class="divider">|</span><span class="role">Director</span></p>

    <ul class="contact-list">
      <li class="contact-item">
        <svg class="contact-icon" viewBox="0 0 22 22" aria-hidden="true">
          <rect width="22" height="22" rx="3" fill="#7cc242"/>
          <path d="M7 5 l3 3 -1.5 1.8 c1 2 2 3 4 4 l1.7 -1.5 3 3 -2 2 c-5 -1 -9 -5 -10 -10z" fill="#ffffff"/>
        </svg>
        0438 760 514
      </li>
      <li class="contact-item">
        <svg class="contact-icon" viewBox="0 0 22 22" aria-hidden="true">
          <rect width="22" height="22" rx="3" fill="#7cc242"/>
          <rect x="4" y="6.5" width="14" height="10" fill="none" stroke="#ffffff" stroke-width="1.6"/>
          <path d="M4 6.5 l7 5.5 7 -5.5" fill="none" stroke="#ffffff" stroke-width="1.6"/>
        </svg>
        Sales@flowbend.com.au
      </li>
    </ul>

    <address class="address">
      17 Dorwell St<br>
      Tallowmere NSW 2794
    </address>
  </section>
</main>
</body>
</html>
```